Residential building / Apartments for sale landing page

I need a website / landing page design for my latest development project - a residential building with 70+ apartments for sale. I need the design in layers in Photoshop/Illustrator/InDesign format with all the icons/shapes/maps/graphic assets in vector format (svg, ai, eps) as much as possible.

I prefer white website and please consider the performance/coding experience. We're not making something suitable only for a design contest with fancy parallax effects and confusing animations. We're trying to create usable and clean UI with good UX.

The website will be custom coded, i.e. I'm not using WordPress.

I know that the existing 3D photos are not good but for now you can use them or replace them with some stock photos. I'm going to create new 3D photos soon.

Real Estate Development

1 page

```html
<!DOCTYPE html>
<html lang="en">
<head>
<meta charset="utf-8">
<title>Tall Pines — Landing Page Presentation</title>
<link href="https://fonts.googleapis.com/css2?family=Poppins:wght@400;500;600;700;800&display=swap" rel="stylesheet">
<style>
:root{
  --green:#8cc63f;
  --green-dark:#6fa828;
  --green-light:#a6d65a;
  --ink:#1e1e1e;
  --dark:#222426;
  --grey:#6b6b6b;
  --line:#e3e3e3;
  --soft:#f4f4f4;
  --white:#ffffff;
}
*{box-sizing:border-box;margin:0;padding:0}
html,body{width:1200px;height:2688px;overflow:hidden}
body{font-family:"Poppins",sans-serif;color:var(--ink);background:var(--green)}
.board{position:relative;width:1200px;height:2688px;overflow:hidden;
  background:radial-gradient(ellipse 900px 700px at 1250px 1300px,var(--green-light) 0 60%,transparent 61%),
             radial-gradient(ellipse 700px 900px at -150px 1900px,#9ad04d 0 55%,transparent 56%),var(--green)}
.brand{position:absolute;top:150px;left:0;width:1200px;text-align:center}
.brand__name{font-size:64px;font-weight:800;color:var(--white);letter-spacing:2px}
.label{position:absolute;top:372px;font-size:20px;font-weight:700;color:var(--white);letter-spacing:1px}
.page{position:absolute;top:412px;width:372px;height:2008px;background:var(--white);overflow:hidden;font-size:5px;line-height:1.5;color:var(--grey);box-shadow:0 10px 30px rgba(0,0,0,.15)}
.page--home{left:200px}
.page--detail{left:628px}
.sec{position:relative;padding:14px 18px}
.ph{border-radius:2px}
.h2{font-size:11px;font-weight:700;color:var(--ink);text-align:center;margin-bottom:10px}
.h2 span{color:var(--green-dark);border-bottom:2px solid var(--green)}
/* hero */
.hero{height:180px;background:var(--soft)}
.nav{display:flex;align-items:center;gap:9px;font-size:4.5px}
.nav__logo{font-weight:700;font-size:6px;color:var(--ink);margin-right:auto}
.nav__cta{background:var(--green);color:var(--white);padding:2px 6px;border-radius:2px}
.hero__text{position:absolute;left:18px;top:48px;width:160px}
.hero__title{font-size:11px;font-weight:700;color:var(--ink);line-height:1.25}
.hero__title em{font-style:normal;color:var(--green-dark)}
.hero__text p{margin:6px 0}
.btn{display:inline-block;background:var(--dark);color:var(--white);padding:3px 10px;font-size:4.5px;border-radius:2px}
.btn--green{background:var(--green)}
.hero__photo{position:absolute;right:0;top:26px;width:170px;height:154px;background:linear-gradient(160deg,#d9e4cf,#7f9a6a 60%,#5c6e52)}
/* project */
.project{height:220px;display:flex;gap:16px;align-items:center}
.project__img{width:130px;height:170px;background:linear-gradient(90deg,#3d3f41,#9aa39a 40%,#7aa84a 70%,#e6e6e6)}
.project__title{font-size:12px;font-weight:700;color:var(--ink);line-height:1.2;border-left:3px solid var(--green);padding-left:6px;margin-bottom:6px}
/* sales */
.sales{height:268px}
.filters{display:flex;gap:6px;justify-content:center;margin-bottom:10px}
.filters span{border:1px solid var(--line);padding:2px 8px}
.cards{display:flex;gap:8px}
.card{flex:1;border:1px solid var(--line)}
.card__img{height:62px;background:linear-gradient(150deg,#cfe0c0,#6f8f5a)}
.card__body{padding:5px}
.card__body b{display:block;color:var(--ink);font-size:6px}
.card__row{display:flex;justify-content:space-between;border-top:1px solid var(--line);padding-top:2px;margin-top:2px}
.pager{display:flex;gap:4px;justify-content:center;margin-top:12px}
.pager i{width:6px;height:6px;border-radius:50%;background:var(--line)}
.pager i:first-child{background:var(--green)}
/* list */
.list{height:200px;background:var(--soft)}
.table{width:100%;border-collapse:collapse;font-size:4.5px;background:var(--white)}
.table th{background:var(--dark);color:var(--white);font-weight:500;padding:3px}
.table td{padding:3px;border-bottom:1px solid var(--line);text-align:center}
.table td:last-child{color:var(--green-dark);font-weight:600}
/* map */
.map{height:228px;display:flex;gap:12px}
.map__text{width:120px}
.map__title{font-size:11px;font-weight:700;color:var(--ink);line-height:1.2;margin:20px 0 8px}
.legend div{display:flex;align-items:center;gap:4px;margin:3px 0}
.legend i{width:6px;height:6px;background:var(--green)}
.map__plan{flex:1;background:radial-gradient(circle at 55% 50%,#b9de86 0 28%,#eef3e8 29%)}
/* facilities */
.facilities{height:160px}
.feats{display:flex;gap:6px;text-align:center}
.feat{flex:1}
.feat svg{width:20px;height:20px;margin-bottom:4px}
.feat b{display:block;color:var(--ink);font-size:5px}
/* construction */
.construction{height:204px;background:var(--dark);color:#bdbdbd}
.construction .h2{color:var(--white)}
.cols{display:grid;grid-template-columns:1fr 1fr;gap:8px 20px}
.cols b{display:block;color:var(--white);font-size:5.5px}
/* location */
.location{height:220px}
.location__map{margin:0 auto;width:270px;height:160px;background:linear-gradient(135deg,#eceeea,#dfe3dc);position:relative}
.location__map svg{position:absolute;left:125px;top:60px;width:20px;height:26px}
/* gallery */
.gallery{height:220px;background:var(--soft)}
.gallery__row{display:flex;gap:8px}
.gallery__row div{flex:1;height:150px;background:linear-gradient(160deg,#a9c9e0,#7c9a66 60%,#5b6b52)}
/* contact */
.contact{height:100px;display:flex;gap:14px;padding-top:10px}
.contact__info{width:110px;font-size:4.5px}
.contact__info b{color:var(--ink);font-size:6px;display:block}
.contact__form{flex:1}
.contact__form .h2{text-align:left;margin-bottom:5px}
.input{height:9px;border:1px solid var(--line);margin-bottom:4px}
/* detail overlay */
.shade{position:absolute;inset:0;background:rgba(40,40,40,.42)}
.modal{position:absolute;left:12px;top:476px;width:340px;height:172px;background:var(--white);padding:12px;display:flex;gap:12px;box-shadow:0 6px 18px rgba(0,0,0,.3)}
.modal__info{width:130px}
.modal__title{font-size:11px;font-weight:700;color:var(--ink);margin-bottom:6px}
.modal__row{display:flex;justify-content:space-between;border-bottom:1px solid var(--line);padding:2px 0}
.modal__row b{color:var(--ink)}
.modal__plan{flex:1;background:linear-gradient(135deg,#f0f4fa,#dfe6f0);border:1px solid var(--line)}
.modal .btn{margin-top:8px}
</style>
</head>
<body>
<div class="board">
  <div class="brand"><div class="brand__name">TALL PINES</div></div>
  <div class="label" style="left:200px">HOME</div>
  <div class="label" style="left:628px">APARTMENT DETAIL</div>

  <!-- HOME -->
  <main class="page page--home">
    <section class="sec hero">
      <nav class="nav"><span class="nav__logo">TALL PINES</span><span>Home</span><span>Project</span><span>Apartments</span><span>Location</span><span>Gallery</span><span class="nav__cta">Contact</span></nav>
      <div class="hero__text">
        <h1 class="hero__title">Sale Of Apartments Directly From The Investor with <em>0% Commission</em></h1>
        <p>Modern homes in a quiet green district, built with care and ready for families who value light and space.</p>
        <span class="btn">Learn more</span>
      </div>
      <div class="hero__photo ph" role="img" aria-label="Rendering of the residential building with green facade"></div>
    </section>
    <section class="sec project">
      <div class="project__img ph" role="img" aria-label="Abstract building facade graphic"></div>
      <div><h2 class="project__title">Project<br>Presentation</h2><p>Seventy bright apartments across six floors, with terraces, garages and shared gardens. Every unit offers open plans and quality finishes throughout the home.</p></div>
    </section>
    <section class="sec sales">
      <h2 class="h2">Apartments/<span>Sales</span></h2>
      <div class="filters"><span>All</span><span>1 Room</span><span>2 Rooms</span><span>3 Rooms</span></div>
      <div class="cards">
        <div class="card"><div class="card__img" role="img" aria-label="Building exterior photo"></div><div class="card__body"><b>Apartment A12</b><div class="card__row"><span>Area</span><span>64 m²</span></div><div class="card__row"><span>Floor</span><span>2</span></div></div></div>
        <div class="card"><div class="card__img" role="img" aria-label="Building exterior photo"></div><div class="card__body"><b>Apartment B04</b><div class="card__row"><span>Area</span><span>52 m²</span></div><div class="card__row"><span>Floor</span><span>1</span></div></div></div>
        <div class="card"><div class="card__img" role="img" aria-label="Building exterior photo"></div><div class="card__body"><b>Apartment C21</b><div class="card__row"><span>Area</span><span>88 m²</span></div><div class="card__row"><span>Floor</span><span>4</span></div></div></div>
      </div>
      <div class="pager"><i></i><i></i><i></i></div>
    </section>
    <section class="sec list">
      <h2 class="h2">Apartments/<span>List</span></h2>
      <table class="table"><tr><th>No.</th><th>Floor</th><th>Rooms</th><th>Area</th><th>Terrace</th><th>Price</th><th>Status</th></tr>
        <tr><td>A10</td><td>1</td><td>2</td><td>54 m²</td><td>6 m²</td><td>98 000</td><td>Available</td></tr>
        <tr><td>A11</td><td>1</td><td>3</td><td>71 m²</td><td>8 m²</td><td>126 000</td><td>Available</td></tr>
        <tr><td>A12</td><td>2</td><td>2</td><td>64 m²</td><td>7 m²</td><td>112 000</td><td>Available</td></tr>
        <tr><td>A13</td><td>2</td><td>1</td><td>38 m²</td><td>5 m²</td><td>72 000</td><td>Reserved</td></tr>
        <tr><td>A14</td><td>3</td><td>3</td><td>80 m²</td><td>9 m²</td><td>139 000</td><td>Available</td></tr>
        <tr><td>A15</td><td>3</td><td>2</td><td>58 m²</td><td>6 m²</td><td>104 000</td><td>Available</td></tr>
        <tr><td>A16</td><td>4</td><td>4</td><td>96 m²</td><td>12 m²</td><td>168 000</td><td>Available</td></tr>
      </table>
    </section>
    <section class="sec map">
      <div class="map__text"><h2 class="map__title">Map/Layout Of<br>The Project With</h2>
        <div class="legend"><div><i></i>Building A</div><div><i></i>Building B</div><div><i></i>Parking</div><div><i></i>Playground</div></div></div>
      <div class="map__plan ph" role="img" aria-label="Site plan of the project with buildings and green areas"></div>
    </section>
    <section class="sec facilities">
      <h2 class="h2">Facilities/<span>Benefits</span></h2>
      <div class="feats">
        <div class="feat"><svg viewBox="0 0 20 20" fill="none" stroke="#6fa828" stroke-width="1.5"><path d="M3 10 10 4l7 6v7H3z"/></svg><b>Quality homes</b>Solid build and finishes</div>
        <div class="feat"><svg viewBox="0 0 20 20" fill="none" stroke="#6fa828" stroke-width="1.5"><rect x="3" y="7" width="14" height="8"/><circle cx="6" cy="16" r="1.5"/><circle cx="14" cy="16" r="1.5"/></svg><b>Garage</b>Private parking spaces</div>
        <div class="feat"><svg viewBox="0 0 20 20" fill="none" stroke="#6fa828" stroke-width="1.5"><circle cx="10" cy="8" r="5"/><path d="M10 13v5"/></svg><b>Green park</b>Gardens around building</div>
        <div class="feat"><svg viewBox="0 0 20 20" fill="none" stroke="#6fa828" stroke-width="1.5"><path d="M4 10l4 4 8-8"/></svg><b>Security</b>Guarded entry all day</div>
        <div class="feat"><svg viewBox="0 0 20 20" fill="none" stroke="#6fa828" stroke-width="1.5"><path d="M10 2a6 6 0 0 1 6 6c0 5-6 10-6 10S4 13 4 8a6 6 0 0 1 6-6z"/></svg><b>Location</b>Near schools and shops</div>
      </div>
    </section>
    <section class="sec construction">
      <h2 class="h2">Construction/<span>Features</span></h2>
      <div class="cols">
        <div><b>Foundation</b>Reinforced concrete slab with full insulation.</div>
        <div><b>Walls</b>Thick brick walls for warmth and quiet rooms.</div>
        <div><b>Windows</b>Triple glazed frames with high energy rating.</div>
        <div><b>Heating</b>Floor heating with smart room thermostats.</div>
        <div><b>Roof</b>Flat green roof with drainage and solar panels.</div>
        <div><b>Lift</b>Quiet elevator serving every floor and garage.</div>
      </div>
    </section>
    <section class="sec location">
      <h2 class="h2">Our<span>Location</span></h2>
      <div class="location__map ph" role="img" aria-label="Street map showing the building location"><svg viewBox="0 0 20 26"><path d="M10 1a8 8 0 0 1 8 8c0 7-8 16-8 16S2 16 2 9a8 8 0 0 1 8-8z" fill="#6fa828"/><circle cx="10" cy="9" r="3" fill="#fff"/></svg></div>
    </section>
    <section class="sec gallery">
      <h2 class="h2">Our<span>Gallery</span></h2>
      <div class="gallery__row"><div class="ph" role="img" aria-label="Building exterior view"></div><div class="ph" role="img" aria-label="Building exterior at dusk"></div></div>
    </section>
    <section class="sec contact">
      <div class="contact__info"><b>TALL PINES</b>Green Street 14, Cityville<br>+00 123 456 789<br>hello@tallpines.example</div>
      <div class="contact__form"><h2 class="h2">Contact <span>Form</span></h2><div class="input"></div><div class="input"></div><span class="btn btn--green">Send</span></div>
    </section>
  </main>

  <!-- APARTMENT DETAIL -->
  <main class="page page--detail">
    <section class="sec hero">
      <nav class="nav"><span class="nav__logo">TALL PINES</span><span>Home</span><span>Project</span><span>Apartments</span><span>Location</span><span>Gallery</span><span class="nav__cta">Contact</span></nav>
      <div class="hero__text">
        <h1 class="hero__title">Sale Of Apartments Directly From The Investor with <em>0% Commission</em></h1>
        <p>Modern homes in a quiet green district, built with care and ready for families who value light and space.</p>
        <span class="btn">Learn more</span>
      </div>
      <div class="hero__photo ph" role="img" aria-label="Rendering of the residential building with green facade"></div>
    </section>
    <section class="sec project">
      <div class="project__img ph" role="img" aria-label="Abstract building facade graphic"></div>
      <div><h2 class="project__title">Project<br>Presentation</h2><p>Seventy bright apartments across six floors, with terraces, garages and shared gardens. Every unit offers open plans and quality finishes throughout the home.</p></div>
    </section>
    <section class="sec sales">
      <h2 class="h2">Apartments/<span>Sales</span></h2>
      <div class="filters"><span>All</span><span>1 Room</span><span>2 Rooms</span><span>3 Rooms</span></div>
    </section>
    <section class="sec list">
      <h2 class="h2">Apartments/<span>List</span></h2>
      <table class="table"><tr><th>No.</th><th>Floor</th><th>Rooms</th><th>Area</th><th>Terrace</th><th>Price</th><th>Status</th></tr>
        <tr><td>A10</td><td>1</td><td>2</td><td>54 m²</td><td>6 m²</td><td>98 000</td><td>Available</td></tr>
        <tr><td>A11</td><td>1</td><td>3</td><td>71 m²</td><td>8 m²</td><td>126 000</td><td>Available</td></tr>
        <tr><td>A12</td><td>2</td><td>2</td><td>64 m²</td><td>7 m²</td><td>112 000</td><td>Available</td></tr>
        <tr><td>A13</td><td>2</td><td>1</td><td>38 m²</td><td>5 m²</td><td>72 000</td><td>Reserved</td></tr>
        <tr><td>A14</td><td>3</td><td>3</td><td>80 m²</td><td>9 m²</td><td>139 000</td><td>Available</td></tr>
        <tr><td>A15</td><td>3</td><td>2</td><td>58 m²</td><td>6 m²</td><td>104 000</td><td>Available</td></tr>
        <tr><td>A16</td><td>4</td><td>4</td><td>96 m²</td><td>12 m²</td><td>168 000</td><td>Available</td></tr>
      </table>
    </section>
    <section class="sec map">
      <div class="map__text"><h2 class="map__title">Map/Layout Of<br>The Project With</h2>
        <div class="legend"><div><i></i>Building A</div><div><i></i>Building B</div><div><i></i>Parking</div><div><i></i>Playground</div></div></div>
      <div class="map__plan ph" role="img" aria-label="Site plan of the project with buildings and green areas"></div>
    </section>
    <section class="sec facilities">
      <h2 class="h2">Facilities/<span>Benefits</span></h2>
      <div class="feats">
        <div class="feat"><svg viewBox="0 0 20 20" fill="none" stroke="#6fa828" stroke-width="1.5"><path d="M3 10 10 4l7 6v7H3z"/></svg><b>Quality homes</b>Solid build and finishes</div>
        <div class="feat"><svg viewBox="0 0 20 20" fill="none" stroke="#6fa828" stroke-width="1.5"><rect x="3" y="7" width="14" height="8"/><circle cx="6" cy="16" r="1.5"/><circle cx="14" cy="16" r="1.5"/></svg><b>Garage</b>Private parking spaces</div>
        <div class="feat"><svg viewBox="0 0 20 20" fill="none" stroke="#6fa828" stroke-width="1.5"><circle cx="10" cy="8" r="5"/><path d="M10 13v5"/></svg><b>Green park</b>Gardens around building</div>
        <div class="feat"><svg viewBox="0 0 20 20" fill="none" stroke="#6fa828" stroke-width="1.5"><path d="M4 10l4 4 8-8"/></svg><b>Security</b>Guarded entry all day</div>
        <div class="feat"><svg viewBox="0 0 20 20" fill="none" stroke="#6fa828" stroke-width="1.5"><path d="M10 2a6 6 0 0 1 6 6c0 5-6 10-6 10S4 13 4 8a6 6 0 0 1 6-6z"/></svg><b>Location</b>Near schools and shops</div>
      </div>
    </section>
    <section class="sec construction">
      <h2 class="h2">Construction/<span>Features</span></h2>
      <div class="cols">
        <div><b>Foundation</b>Reinforced concrete slab with full insulation.</div>
        <div><b>Walls</b>Thick brick walls for warmth and quiet rooms.</div>
        <div><b>Windows</b>Triple glazed frames with high energy rating.</div>
        <div><b>Heating</b>Floor heating with smart room thermostats.</div>
        <div><b>Roof</b>Flat green roof with drainage and solar panels.</div>
        <div><b>Lift</b>Quiet elevator serving every floor and garage.</div>
      </div>
    </section>
    <section class="sec location">
      <h2 class="h2">Our<span>Location</span></h2>
      <div class="location__map ph" role="img" aria-label="Street map showing the building location"><svg viewBox="0 0 20 26"><path d="M10 1a8 8 0 0 1 8 8c0 7-8 16-8 16S2 16 2 9a8 8 0 0 1 8-8z" fill="#6fa828"/><circle cx="10" cy="9" r="3" fill="#fff"/></svg></div>
    </section>
    <section class="sec gallery">
      <h2 class="h2">Our<span>Gallery</span></h2>
      <div class="gallery__row"><div class="ph" role="img" aria-label="Building exterior view"></div><div class="ph" role="img" aria-label="Building exterior at dusk"></div></div>
    </section>
    <section class="sec contact">
      <div class="contact__info"><b>TALL PINES</b>Green Street 14, Cityville<br>+00 123 456 789<br>hello@tallpines.example</div>
      <div class="contact__form"><h2 class="h2">Contact <span>Form</span></h2><div class="input"></div><div class="input"></div><span class="btn btn--green">Send</span></div>
    </section>
    <div class="shade"></div>
    <div class="modal">
      <div class="modal__info">
        <h3 class="modal__title">Apartment A12</h3>
        <div class="modal__row"><span>Floor</span><b>2</b></div>
        <div class="modal__row"><span>Rooms</span><b>2</b></div>
        <div class="modal__row"><span>Living area</span><b>64 m²</b></div>
        <div class="modal__row"><span>Terrace</span><b>7 m²</b></div>
        <div class="modal__row"><span>Price</span><b>112 000</b></div>
        <span class="btn btn--green">Send inquiry</span>
      </div>
      <div class="modal__plan ph" role="img" aria-label="Floor plan of apartment A12"></div>
    </div>
  </main>
</div>
</body>
</html>
```